Clarinet Past Midnight: mini recital & soiree

I need a poster design for a recital I'm doing next Friday April 25. It's an "after party" from 10 - 1am where I'll be playing a 30 min program followed by a DJ and there'll be food wine etc. I want to see a very "sexy" kind of poster. Modern with a "south beach" kind of art deco feel but without the really cheesy connotation that south beach sometimes has (if that makes any sense). I've included the link for the Gatherloop event so you can get an idea of the feel I want.

Cheers!

https://www.gatherloop.example/events/315906274821650/

Target Market(s)

College Students at the Halvern State College

South Beach-ians

Industry/Entity Type

Events

Colors

Designer to choose colors to be used in the design.

Requirements
Must have
• Title of event..
Date..
Location..
Food / Beverage served..
DJ Ostrova..

```html
<!DOCTYPE html>
<html lang="en">
<head>
<meta charset="utf-8">
<title>Clarinet Past Midnight – Mini Recital &amp; Soirée</title>
<link rel="stylesheet" href="https://fonts.googleapis.com/css2?family=Bebas+Neue&family=Poiret+One&family=Raleway:wght@300;400;500&display=swap">
<style>
  :root {
    --page: #ececea;
    --band: #ffffff;
    --night: #000000;
    --ink-dark: #111111;
    --ink-light: #ffffff;
    --plum: #8e2a8f;
    --coral: #ef6f48;
    --sky: #8fc6ee;
    --rose: #f07c86;
    --lime: #a9d35b;
  }
  * { box-sizing: border-box; margin: 0; padding: 0; }
  html, body { width: 1200px; height: 1152px; overflow: hidden; }
  body { background: var(--page); position: relative; }

  .poster {
    position: absolute; left: 210px; top: 24px;
    width: 780px; height: 1104px;
    background: var(--night);
    overflow: hidden;
  }
  .poster__band {
    position: absolute; left: 0; top: 0; width: 100%; height: 180px;
    background: var(--band);
  }
  .poster__instrument {
    position: absolute; left: 8px; top: 192px; width: 312px; height: 892px;
  }
  .eyebrow {
    position: absolute; left: 30px; top: 80px;
    font-family: "Raleway", sans-serif; font-weight: 400;
    font-size: 31px; letter-spacing: 1px; color: var(--plum);
  }
  .title {
    position: absolute; right: 42px;
    font-family: "Poiret One", sans-serif; font-weight: 400;
    font-size: 112px; line-height: 1; text-align: right; letter-spacing: 2px;
  }
  .title--top { top: 84px; color: var(--ink-dark); }
  .title--bottom { top: 190px; color: var(--ink-light); }

  .lineup { position: absolute; right: 51px; text-align: right; }
  .lineup__headline {
    top: 494px; font-family: "Bebas Neue", sans-serif;
    font-size: 58px; line-height: 1; color: var(--ink-light); letter-spacing: 0.5px;
  }
  .lineup__tag {
    font-family: "Raleway", sans-serif; font-weight: 300; color: var(--coral);
  }
  .lineup__tag--live { top: 552px; font-size: 38px; }
  .lineup__dj {
    top: 612px; font-family: "Raleway", sans-serif; font-weight: 500;
    font-size: 56px; line-height: 1; color: var(--ink-light); letter-spacing: 1px;
  }
  .lineup__tag--set { top: 672px; font-size: 15px; letter-spacing: 1px; }

  .details {
    position: absolute; right: 51px; top: 998px; text-align: right;
    font-family: "Raleway", sans-serif;
  }
  .details__when { font-size: 25px; font-weight: 400; color: var(--sky); letter-spacing: 1px; line-height: 1.2; }
  .details__where { font-size: 14px; color: var(--rose); letter-spacing: 0.5px; line-height: 1.5; }
  .details__menu { font-size: 14px; color: var(--lime); letter-spacing: 0.5px; line-height: 1.4; }
</style>
</head>
<body>
  <main class="poster">
    <div class="poster__band"></div>

    <svg class="poster__instrument" role="img" aria-label="Photograph of a polished silver clarinet-family instrument on black" viewBox="0 0 312 892" preserveAspectRatio="none">
      <defs>
        <linearGradient id="metal" x1="0" y1="0" x2="1" y2="1">
          <stop offset="0" stop-color="#3a3a3a"/>
          <stop offset="0.45" stop-color="#8a8a8a"/>
          <stop offset="1" stop-color="#1c1c1c"/>
        </linearGradient>
      </defs>
      <rect width="312" height="892" fill="url(#metal)" opacity="0.55"/>
    </svg>

    <p class="eyebrow">CLARINET</p>
    <h1 class="title title--top">PAST</h1>
    <h1 class="title title--bottom">MIDNIGHT</h1>

    <p class="lineup lineup__headline">MINI RECITAL &amp; SOIRÉE</p>
    <p class="lineup lineup__tag lineup__tag--live">LIVE</p>
    <p class="lineup lineup__dj">DJ OSTROVA</p>
    <p class="lineup lineup__tag lineup__tag--set">DJ SET FOR THE NIGHT</p>

    <section class="details">
      <p class="details__when">FRIDAY, APRIL 25 AT 10:00PM - 1:00AM</p>
      <p class="details__where">THORNFIELD ALUMNI CENTER- HALVERN STATE COLLEGE</p>
      <p class="details__menu">FOOD / WINE / DRINK WILL BE SERVED!!</p>
    </section>
  </main>
</body>
</html>
```